New Fun, Positive, energised looking Business Card Needed for High Achiever Coach

I am looking for a two sided full colour business card. I am self employed and have recently re branded my 1-2-1 work re-vitalising high achievers. My target client base for these cards is therefore high achievers - usually aged 40 -55, they are often entrepreneurs, CEO or work in banking and finance and 2/3 are male. I work with them on 90 day or 6 month coaching programs to help them live their success in a healthier, more sustainable and fulfiiled way. They pay for this privately so though they are corporate types the cards need not look 'corporate'. I want to portray the idea of transformation, vitality and re-connecting.
You can get a feel for the look I like on my new website: morvenlisk.co.uk
I want to use this logo with strapline (Re-Vitalising High Achievers) (I purchased off Logoharbor) and font/ colours (the turquoise and green).
Details to include on the card:
www.morvenlisk.co.uk
+44 7915 302618
morven@morvenlisk.co.uk
skype: morvenlisk
I'd also like to include:
Do you struggle to switch off? Want to be healthier and feel fitter? Want closer relationships? More clarity over the direction you are headed? I can help you do these things using integrated mind-body techniques. Visit morvenlisk.co.uk TODAY to apply for a FREE Breakthrough session.
BUT if that is too much text for a card I am open to advice/ammendments.
Updates
Thanks for your design - I am considering them. PLease change the wording to :

```html
<!DOCTYPE html>
<html lang="en">
<head>
<meta charset="utf-8">
<title>Morven Lisk – Business Card</title>
<link rel="stylesheet" href="https://fonts.googleapis.com/css2?family=Arvo:wght@700&family=Source+Sans+3:wght@400;700&family=Yellowtail&display=swap">
<style>
  :root {
    --backdrop: #646568;
    --card-white: #ffffff;
    --card-edge: #d9dadb;
    --brand-green: #63bf6c;
    --brand-turquoise: #1fa2c6;
    --contact-grey: #9a9b9d;
    --faint-green: rgba(99, 191, 108, 0.12);
    --faint-white: rgba(255, 255, 255, 0.14);
    --text-light: #ffffff;
  }
  * { box-sizing: border-box; margin: 0; padding: 0; }
  html, body {
    width: 991px;
    height: 1200px;
    overflow: hidden;
    background: var(--backdrop);
  }
  .canvas {
    position: relative;
    width: 991px;
    height: 1200px;
  }
  .card {
    position: absolute;
    left: 32px;
    width: 939px;
    border-radius: 32px;
    overflow: hidden;
  }
  .card--front {
    top: 48px;
    height: 538px;
    background: var(--card-white);
    border: 3px solid var(--card-edge);
  }
  .card--back {
    top: 642px;
    height: 535px;
    background: var(--brand-green);
  }
  .faint-circle {
    position: absolute;
    border-radius: 50%;
  }
  .card--front .faint-circle {
    left: 80px;
    top: -40px;
    width: 280px;
    height: 280px;
    border: 34px solid var(--faint-green);
  }
  .card--back .faint-circle {
    left: 560px;
    top: -60px;
    width: 300px;
    height: 300px;
    border: 34px solid var(--faint-white);
  }
  .brand {
    position: absolute;
    left: 500px;
    top: 120px;
    width: 420px;
    text-align: center;
  }
  .brand__circle {
    display: block;
    margin: 0 auto 40px;
    width: 150px;
    height: 150px;
    border-radius: 50%;
    border: 14px solid var(--brand-green);
  }
  .brand__name {
    font-family: "Arvo", serif;
    font-weight: 700;
    font-size: 50px;
    line-height: 1;
    color: var(--brand-turquoise);
  }
  .brand__strapline {
    margin-top: 16px;
    font-family: "Yellowtail", cursive;
    font-size: 32px;
    line-height: 1;
    color: var(--brand-turquoise);
  }
  .contact {
    position: absolute;
    left: 48px;
    top: 355px;
    list-style: none;
    font-family: "Source Sans 3", sans-serif;
    font-size: 26px;
    line-height: 1;
    color: var(--contact-grey);
  }
  .contact__item {
    display: flex;
    align-items: center;
    height: 32px;
  }
  .contact__icon {
    width: 22px;
    height: 22px;
    margin-right: 12px;
    fill: var(--contact-grey);
    flex: none;
  }
  .pitch {
    position: absolute;
    left: 40px;
    right: 40px;
    top: 176px;
    text-align: center;
    font-family: "Source Sans 3", sans-serif;
    font-size: 23px;
    line-height: 32px;
    color: var(--text-light);
  }
  .pitch__link {
    font-weight: 700;
    font-size: 26px;
  }
</style>
</head>
<body>
<main class="canvas">
  <section class="card card--front" aria-label="Card front">
    <span class="faint-circle" aria-hidden="true"></span>
    <div class="brand">
      <span class="brand__circle" aria-hidden="true"></span>
      <p class="brand__name">Morven Lisk</p>
      <p class="brand__strapline">Re-Vitalising High Achievers</p>
    </div>
    <ul class="contact">
      <li class="contact__item">
        <svg class="contact__icon" viewBox="0 0 24 24" aria-hidden="true"><path d="M6.6 10.8a15.1 15.1 0 0 0 6.6 6.6l2.2-2.2c.3-.3.7-.4 1-.2 1.1.4 2.3.6 3.6.6.6 0 1 .4 1 1V20c0 .6-.4 1-1 1C10.6 21 3 13.4 3 4c0-.6.4-1 1-1h3.5c.6 0 1 .4 1 1 0 1.3.2 2.5.6 3.6.1.3 0 .7-.2 1z"/></svg>
        +44 7915 302618
      </li>
      <li class="contact__item">
        <svg class="contact__icon" viewBox="0 0 24 24" aria-hidden="true"><circle cx="12" cy="12" r="9"/></svg>
        morvenlisk
      </li>
      <li class="contact__item">
        <svg class="contact__icon" viewBox="0 0 24 24" aria-hidden="true"><path d="M12 2a10 10 0 1 0 0 20 10 10 0 0 0 0-20zm6.9 6h-2.9a15.7 15.7 0 0 0-1.4-3.6A8 8 0 0 1 18.9 8zM12 4c.8 1.2 1.5 2.5 1.9 4h-3.8c.4-1.5 1.1-2.8 1.9-4zM4.3 14a8.2 8.2 0 0 1 0-4h3.4a16.5 16.5 0 0 0 0 4zm.8 2h2.9c.3 1.3.8 2.5 1.4 3.6A8 8 0 0 1 5.1 16zM8 8H5.1a8 8 0 0 1 4.3-3.6C8.8 5.5 8.3 6.7 8 8zm4 12c-.8-1.2-1.5-2.5-1.9-4h3.8c-.4 1.5-1.1 2.8-1.9 4zm2.3-6H9.7a14.7 14.7 0 0 1 0-4h4.6a14.7 14.7 0 0 1 0 4zm.3 5.6c.6-1.1 1.1-2.3 1.4-3.6h2.9a8 8 0 0 1-4.3 3.6zm1.7-5.6a16.5 16.5 0 0 0 0-4h3.4a8.2 8.2 0 0 1 0 4z"/></svg>
        www.morvenlisk.co.uk
      </li>
      <li class="contact__item">
        <svg class="contact__icon" viewBox="0 0 24 24" aria-hidden="true"><path d="M3 5h18v14H3zm2 2v.5l7 4.5 7-4.5V7l-7 4.5z"/></svg>
        morven@morvenlisk.co.uk
      </li>
    </ul>
  </section>

  <section class="card card--back" aria-label="Card back">
    <span class="faint-circle" aria-hidden="true"></span>
    <p class="pitch">
      Do you struggle to switch off? Want to be healthier and feel fitter? Want closer<br>
      relationships? More clarity over the direction you are headed? I can help you do<br>
      these things using integrated mind-body techniques.<br>
      Visit <span class="pitch__link">morvenlisk.co.uk</span><br>
      TODAY to apply for a FREE Breakthrough session.
    </p>
  </section>
</main>
</body>
</html>
```